BRN website video quote promotion tiles

We are promoting vehicle leasing by video, which contains several quotation examples imported from the video. We must re-vamp the quotation tiles, contact boxes, and contact form. The first tile is generated from the video, so this must be a separate project. We are looking for a welcoming, professional flow and leave color choices to design with an emphasis on communication prompts, and additional prompts in the design would be welcome.

Target Market(s)

Any Customer interaction from the tile quotes, contact, call, message,

Industry/Entity Type

vehicle leasing

Coding

Coded - Design and coding required

Number of Pages Required

1 page

Colors

Designer to choose colors to be used in the design.

Requirements
Must have
• emphasis on point of contact and visual impact on quote tile excluding main one
Should not have
• changes to the quote structure as these imported from video pricing no changes to main image as this template which can addressed as separate project

```html
<!DOCTYPE html>
<html lang="en">
<head>
<meta charset="utf-8">
<title>BRN Quote Tiles</title>
<link rel="stylesheet" href="https://fonts.googleapis.com/css2?family=Lato:wght@300;400;700;900&display=swap">
<style>
:root{
  --page:#dcdcdc;
  --white:#ffffff;
  --orange:#e07b2a;
  --orange-deep:#df7a2e;
  --yellow:#e9bd42;
  --green:#25d366;
  --red:#f0241b;
  --text:#444444;
  --overlay:#3b3b3b;
}
*{box-sizing:border-box;margin:0;padding:0}
html,body{width:1200px;height:363px;overflow:hidden;background:var(--page);font-family:'Lato',sans-serif}
.canvas{position:relative;width:1200px;height:363px}
.abs{position:absolute}

/* tiles panel */
.tiles-panel{left:13px;top:10px;width:584px;height:329px;background:var(--white)}
.tile{background:var(--white);box-shadow:0 1px 5px rgba(0,0,0,.15)}
.tile-title{color:var(--orange);font-size:12.5px;font-weight:400;letter-spacing:.2px}
.tile-row{font-size:9.2px;color:var(--text);font-weight:400}
.not-maintained{color:var(--red);font-size:9.2px}
.pill{background:var(--white);border-radius:7px;font-size:6.5px;color:#111;display:flex;align-items:center;justify-content:center;font-weight:400}
.price{color:var(--white);font-weight:900}
.btn{border-radius:11px;display:flex;align-items:center;color:var(--white);font-size:6.5px;font-weight:400;padding-left:8px}
.btn-contact{background:var(--orange)}
.btn-chat{background:var(--green)}
.btn-icon{position:absolute;right:2px;top:2px;width:16px;height:16px;border-radius:50%;background:var(--white)}
.btn-icon svg{width:16px;height:16px}
.slant-label{font-size:6.5px;color:var(--white);line-height:23px;height:23px;text-align:center;white-space:nowrap}

/* modal */
.modal-backdrop{left:606px;top:13px;width:584px;height:328px;background:var(--overlay);overflow:hidden}
.modal{left:621px;top:23px;width:554px;height:310px;background:var(--white)}
.modal-head{position:absolute;left:0;top:0;width:100%;height:36px;background:var(--orange-deep);color:var(--white);font-weight:700;font-size:16px;display:flex;align-items:center;justify-content:center;padding-right:14px}
.close{position:absolute;right:15px;top:10px;width:21px;height:21px;border-radius:50%;background:var(--white)}
.field{position:absolute;left:61px;width:433px;background:var(--white);border-radius:16px;box-shadow:0 1px 5px rgba(0,0,0,.12);font-size:8px;color:#555;display:flex;align-items:center;padding-left:13px}
.field svg{width:6px;height:6px;margin-right:6px}
.field-message{align-items:flex-start;padding-top:14px}
.submit{position:absolute;left:241px;top:258px;width:73px;height:29px;border-radius:15px;background:linear-gradient(90deg,var(--orange),var(--yellow));color:var(--white);font-size:8px;font-weight:700;display:flex;align-items:center;justify-content:center;box-shadow:0 2px 5px rgba(224,123,42,.35)}
</style>
</head>
<body>
<div class="canvas">

  <section class="tiles-panel abs">

    <!-- tile one -->
    <article class="tile abs" style="left:14px;top:28px;width:182px;height:242px">
      <svg class="abs" style="left:0;top:0" width="182" height="100" viewBox="0 0 182 100">
        <defs><linearGradient id="gy" x1="0" x2="1"><stop offset="0" stop-color="#e9b83f"/><stop offset="1" stop-color="#ebc048"/></linearGradient></defs>
        <path d="M0 0H182V98Q182 78 160 78H14L0 71Z" fill="url(#gy)"/>
      </svg>
      <div class="price abs" style="left:0;width:182px;top:11px;text-align:center;font-size:26px">£247.33</div>
      <div class="pill abs" style="left:68px;top:47px;width:50px;height:20px">PLUS VAT</div>
      <div class="tile-title abs" style="left:18px;top:101px">CONTRACT HIRE</div>
      <svg class="abs" style="left:17px;top:117px" width="14" height="64" viewBox="0 0 14 64">
        <g fill="#dcdcdc"><circle cx="7" cy="7" r="6"/><circle cx="7" cy="30" r="6"/><circle cx="7" cy="53" r="6"/></g>
        <g stroke="#fff" stroke-width="1.3" fill="none"><path d="M4 7h6M8 5l2 2-2 2"/><path d="M4 30h6M8 28l2 2-2 2"/><path d="M4 53h6M8 51l2 2-2 2"/></g>
      </svg>
      <div class="tile-row abs" style="left:39px;top:119px">3 years</div>
      <div class="tile-row abs" style="left:41px;top:142px">9+35</div>
      <div class="tile-row abs" style="left:39px;top:165px">10K miles annually</div>
      <div class="not-maintained abs" style="left:20px;top:186px">Not Maintained</div>
      <div class="btn btn-contact abs" style="left:16px;top:204px;width:78px;height:20px">CONTACT US
        <span class="btn-icon"><svg viewBox="0 0 16 16"><path d="M5 4h5v8H5z" fill="none" stroke="#555" stroke-width=".8"/><path d="M6 6h3M6 8h3M6 10h2M9 11l3-5" stroke="#555" stroke-width=".7"/></svg></span></div>
      <div class="btn btn-chat abs" style="left:99px;top:204px;width:69px;height:20px">CHATLINE
        <span class="btn-icon"><svg viewBox="0 0 16 16"><circle cx="8" cy="8" r="5" fill="var(--green)"/></svg></span></div>
    </article>

    <!-- tile two -->
    <article class="tile abs" style="left:203px;top:28px;width:182px;height:242px">
      <div class="abs" style="left:0;top:0;width:182px;height:64px;background:linear-gradient(90deg,#e07d2f,#e9b83f)"></div>
      <div class="pill abs" style="left:68px;top:10px;width:50px;height:20px">PLUS VAT</div>
      <div class="abs" style="left:36px;top:37px;width:115px;height:52px;background:#fff;border:1px solid var(--orange);border-radius:2px;display:flex;align-items:center;justify-content:center;color:var(--orange);font-weight:900;font-size:24.5px">£247.33</div>
      <div class="tile-title abs" style="left:0;width:182px;text-align:center;top:101px">CONTRACT HIRE</div>
      <svg class="abs" style="left:15px;top:115px" width="16" height="66" viewBox="0 0 16 66">
        <g stroke="var(--orange)" stroke-width="2.2" fill="none"><path d="M1 7l4 4 9-8"/><path d="M1 31l4 4 9-8"/><path d="M1 54l4 4 9-8"/></g>
      </svg>
      <div class="tile-row abs" style="left:39px;top:119px">3 years</div>
      <div class="tile-row abs" style="left:41px;top:142px">9+35</div>
      <div class="tile-row abs" style="left:39px;top:165px">10K miles annually</div>
      <div class="not-maintained abs" style="left:20px;top:186px">Not Maintained</div>
      <div class="btn btn-contact abs" style="left:16px;top:204px;width:78px;height:20px;border-radius:3px">CONTACT US
        <span class="btn-icon" style="border-radius:2px;right:1px;top:1px;width:18px;height:18px"><svg viewBox="0 0 16 16"><path d="M5 4h5v8H5z" fill="none" stroke="#555" stroke-width=".8"/><path d="M6 6h3M6 8h3M6 10h2M9 11l3-5" stroke="#555" stroke-width=".7"/></svg></span></div>
      <div class="btn btn-chat abs" style="left:99px;top:204px;width:78px;height:20px;border-radius:3px">CHATLINE
        <span class="btn-icon" style="border-radius:2px;right:1px;top:1px;width:18px;height:18px"><svg viewBox="0 0 16 16"><circle cx="8" cy="8" r="5" fill="var(--green)"/></svg></span></div>
    </article>

    <!-- tile three -->
    <article class="tile abs" style="left:391px;top:37px;width:183px;height:262px"></article>
    <div class="abs" style="left:399px;top:48px;width:169px;height:241px;border:1.2px solid var(--orange)"></div>
    <div class="abs" style="left:400px;top:18px;width:167px;height:60px;border-radius:9px 9px 0 0;background:linear-gradient(90deg,#e07d2f,#e9b83f)"></div>
    <div class="abs" style="left:407px;top:28px;width:154px;height:60px;background:linear-gradient(90deg,#e07d2f,#e9b83f);box-shadow:0 2px 5px rgba(0,0,0,.15)"></div>
    <div class="pill abs" style="left:459px;top:31px;width:50px;height:20px">PLUS VAT</div>
    <svg class="abs" style="left:459px;top:56px" width="64" height="64" viewBox="0 0 64 64">
      <defs><linearGradient id="gc" x1="0" y1="1" x2="1" y2="0"><stop offset="0" stop-color="#e07d2f"/><stop offset="1" stop-color="#e9b83f"/></linearGradient></defs>
      <path d="M3 32a29 29 0 0 0 58 0" fill="none" stroke="var(--orange)" stroke-width="4"/>
      <circle cx="32" cy="30" r="27" fill="#fff"/>
      <circle cx="32" cy="30" r="21" fill="url(#gc)"/>
    </svg>
    <div class="price abs" style="left:459px;width:64px;top:79px;text-align:center;font-size:9px">£247.33</div>
    <div class="tile-title abs" style="left:391px;width:183px;text-align:center;top:129px">CONTRACT HIRE</div>
    <svg class="abs" style="left:434px;top:144px" width="44" height="66" viewBox="0 0 44 66">
      <g stroke="var(--orange)" stroke-width="2.2" fill="none"><path d="M25 7l4 4 9-8"/><path d="M28 29l4 4 9-8"/><path d="M1 54l4 4 9-8"/></g>
    </svg>
    <div class="tile-row abs" style="left:481px;top:147px">3 years</div>
    <div class="tile-row abs" style="left:485px;top:169px">9+35</div>
    <div class="tile-row abs" style="left:458px;top:193px">10K miles annually</div>
    <div class="not-maintained abs" style="left:453px;top:211px">Not Maintained</div>
    <svg class="abs" style="left:443px;top:231px" width="106" height="54" viewBox="0 0 106 54">
      <path d="M7 0H73L66 23H0Z" fill="var(--orange)"/>
      <path d="M73 0H93L86 23H66Z" fill="#fff" stroke="#ddd" stroke-width=".5"/>
      <path d="M7 29H73L66 52H0Z" fill="var(--green)"/>
      <path d="M73 29H93L86 52H66Z" fill="#fff" stroke="#ddd" stroke-width=".5"/>
      <circle cx="79.5" cy="40.5" r="5" fill="var(--green)"/>
      <g stroke="#555" stroke-width=".8" fill="none"><path d="M76 7h5v8h-5z"/><path d="M77 9h3M77 11h3M80 14l3-5"/></g>
    </svg>
    <div class="slant-label abs" style="left:443px;top:231px;width:70px">CONTACT US</div>
    <div class="slant-label abs" style="left:443px;top:260px;width:70px">CHATLINE</div>
  </section>

  <!-- contact form overlay -->
  <section class="modal-backdrop abs">
    <div class="abs" style="left:0;top:0;width:584px;height:83px;background:linear-gradient(90deg,#6b4a2a,#7a5a30);opacity:.7"></div>
    <div class="abs" style="left:0;top:233px;width:584px;height:40px;background:#4a3a2c;opacity:.6"></div>
  </section>

  <section class="modal abs" aria-label="Contact form">
    <header class="modal-head">Please Submit&nbsp; Your Contact Deatils</header>
    <svg class="close" viewBox="0 0 21 21"><path d="M7 7l7 7M14 7l-7 7" stroke="var(--orange)" stroke-width="2.4" stroke-linecap="round"/></svg>
    <div class="field" style="top:64px;height:35px"><svg viewBox="0 0 6 6"><circle cx="3" cy="1.8" r="1.5" fill="#bbb"/><path d="M0 6a3 2.5 0 0 1 6 0z" fill="#bbb"/></svg>Enter Your Name</div>
    <div class="field" style="top:103px;height:35px"><svg viewBox="0 0 6 6"><rect x="0" y="1" width="6" height="4" fill="none" stroke="#bbb" stroke-width=".8"/><path d="M0 1l3 2 3-2" fill="none" stroke="#bbb" stroke-width=".7"/></svg>Enter Email Address</div>
    <div class="field" style="top:143px;height:34px"><svg viewBox="0 0 6 6"><path d="M1 0l1.4 1.4-.7 1a4 4 0 0 0 1.9 1.9l1-.7L6 5 5 6C2 6 0 4 0 1z" fill="#bbb"/></svg>Enter Phone Number</div>
    <div class="field field-message" style="top:182px;height:65px"><svg viewBox="0 0 6 6"><rect x=".4" y=".4" width="4.2" height="5.2" fill="none" stroke="#bbb" stroke-width=".7"/><path d="M2.5 4.5l3-3.5" stroke="#bbb" stroke-width=".8"/></svg>Enter Your Message</div>
    <div class="submit">SUBMIT</div>
  </section>

</div>
</body>
</html>
```